Security and Technology Website - Bold and Confident, Something Unexpected

Maple Wren Systems is launching its first website and we need a great design to bring our brand to life and generate DTC and B2B leads.

We have a good logo, but I am struggling with the creative vision to bring it all together. While our industry is Alarm Systems and Technology, we want to create a site that is more friendly and less 'typical' than your standard IT sites.

It Must:
1. Appeal to both men and women. The logo is a bit masculine, so the colors and icons must soften this.
2. Feel modern - we need to convey that we we use the latest technology.
3. Feel a bit high-end. We are not a budget solution.
4. Have a distinct iconography and photo treatment.
5. Feel layered - not just a series of stacked horizontal modules.

It Should Not:
1. Feel like your typical IT website.

Here are resources to get you started!
• Staging Site:
https://maple-wren-systems.shopfrontdemo.example/
Password: Piper

•Brand Guide: https://www.layoutboard.example/design/QKRmWpLcT4V/hNbq8Yf2-ZsKeRtDw7xp-QE/edit?utm_content=QKRmWpLcT4V&utm_campaign=designshare&utm_medium=link2&utm_source=sharebutton

• Logo and Fonts and Photos: :https://files.cloudlocker.example/folders/7HtPqWmZc3Kd9RbLx2VnYs8FgJe4UoAiT?usp=sharing

• Design Inspiration (don't feel limited by this): https://www.layoutboard.example/design/QKTnHsVbWe8/p7MfRz31xYqLcKdTu9GNBw/edit?utm_content=QKTnHsVbWe8&utm_campaign=designshare&utm_medium=link2&utm_source=sharebutton

______________

The winner will be asked to provide design files and finished PNGs of the overall design file, backgrounds, photo treatments/frames, and icons.

The winner will likely be engaged for a phase 2 to build out a product page.

Industry/Entity Type

Alarm Systems, Home Theatres, and Commercial IT Networking

Number of Pages Required

1 page

Font styles to use
Sans Serif

Colors
0054AA
0677BA
7BADD7
CADEEF
E8F1F8
0094D4
00A9DD
6FCCEA
C7EBF8
E9F6FB
EB3D1F
EC4F4E
F09395
F8D3D4
FCEDEE

Requirements
Must have
• 1. Appeal to both men and women. The logo is a bit masculine, so the colors and icons must soften this. 2. Feel modern - we need to convey that we we use the latest technology. 3. Feel a bit high-end. We are not a budget solution. 4. Have a distinct iconography and photo treatment. 5. Feel layered - not just a series of stacked horizontal modules.
Should not have
• 1. Should not feel like just another IT website.

```html
<!DOCTYPE html>
<html lang="en">
<head>
<meta charset="utf-8">
<title>Maple Wren Systems — Safer. Smarter. Faster.</title>
<link href="https://fonts.googleapis.com/css2?family=Russo+One&family=Poppins:wght@400;500;600;700&display=swap" rel="stylesheet">
<style>
:root{
  --red:#EB3D1F; --red2:#e3202a; --red-soft:#F8D3D4; --blush:#FCEDEE;
  --navy:#0b3f86; --blue:#0054AA; --blue2:#0677BA; --sky:#0094D4; --cyan:#00A9DD;
  --ice:#C7EBF8; --ice2:#E9F6FB; --mist:#E8F1F8; --grey:#ececef; --text:#1f2a3d;
}
*{box-sizing:border-box;margin:0;padding:0}
html,body{width:1200px;height:3973px;overflow:hidden}
body{position:relative;font-family:'Poppins',sans-serif;color:var(--text);background:#f6fafd}
.abs{position:absolute}

/* top bar */
.topbar{left:0;top:0;width:1200px;height:37px;background:var(--red2);overflow:hidden}
.topbar .slant{left:960px;top:0;width:260px;height:37px;background:linear-gradient(90deg,var(--blue2),var(--blue));transform:skewX(-35deg)}
.topbar nav{left:230px;top:9px;display:flex;gap:90px}
.topbar nav span{font-family:'Russo One',sans-serif;color:#fff;font-size:15px;letter-spacing:1.5px}
.social{display:flex;gap:16px}
.social i{display:block;width:16px;height:16px;border:2px solid #fff;border-radius:2px}

/* header */
.header{left:0;top:37px;width:1200px;height:111px;background:#fff}
.brand{display:flex;align-items:center;gap:8px}
.brand b{display:block;flex:none;width:14px;height:14px;background:var(--red2);border-radius:50%}
.brand span{font-family:'Russo One',sans-serif;color:var(--blue);font-size:17px;line-height:20px}
.mainnav{left:230px;top:45px;display:flex;gap:34px;font-size:13px;font-weight:500;color:var(--blue);white-space:nowrap}
.quote-pill{left:991px;top:34px;width:152px;height:38px;border-radius:20px;background:linear-gradient(90deg,var(--red2),var(--blue));color:#fff;font-family:'Russo One',sans-serif;font-size:12.5px;display:flex;align-items:center;justify-content:center;letter-spacing:.5px}

/* hero */
.hero{left:0;top:148px;width:1200px;height:500px}
.hero-copy{left:0;top:180px;width:1200px;text-align:center;color:#fff}
.kicker{font-size:14px;font-weight:500;letter-spacing:.5px}
.big{font-family:'Russo One',sans-serif;font-size:78px;line-height:92px;letter-spacing:3px}
.sub{font-size:23px;font-weight:500;letter-spacing:1px;margin-top:12px}

/* service cards */
.svc{top:676px;height:404px;border-radius:14px;padding:28px 16px;overflow:hidden}
.svc h3{font-family:'Russo One',sans-serif;font-size:15px;letter-spacing:.5px;margin-bottom:12px;white-space:nowrap}
.svc ul{list-style:none;font-size:13.5px;line-height:21px;font-weight:500}
.svc li:before{content:"• ";}
.svc .ph{position:absolute;left:18px;right:18px;bottom:22px;height:218px;border-radius:14px}
.svc .go{position:absolute;right:26px;bottom:28px;width:28px;height:28px;border-radius:50%}
.svc-red{left:148px;width:300px;background:var(--red2);color:#fff;box-shadow:0 12px 24px rgba(0,0,0,.18)}
.svc-ice{background:var(--ice);color:var(--blue)}

/* connect */
.h2red{font-family:'Russo One',sans-serif;color:var(--red2);font-size:33px;letter-spacing:2px;text-align:center;width:1200px;left:0}
.band{left:0;top:1352px;width:1200px;height:470px;background:linear-gradient(135deg,#0a5db8,#0a86d8 60%,#1a9ce6)}
.feat{top:1254px;width:159px;height:216px;background:#fff;border-radius:8px;box-shadow:0 6px 16px rgba(0,40,90,.18);text-align:center;padding:18px 12px}
.feat svg{width:42px;height:42px;margin-bottom:6px}
.feat h4{font-family:'Russo One',sans-serif;color:var(--blue);font-size:15.5px;line-height:19px;letter-spacing:1px;margin-bottom:8px}
.feat p{font-size:9.5px;line-height:12px;color:#8893a3}
.monitor{left:0;top:1500px;width:1200px;text-align:center;color:#fff}
.monitor h2{font-family:'Russo One',sans-serif;font-size:31px;line-height:42px;letter-spacing:2px}
.monitor p{font-size:11px;line-height:16px;width:540px;margin:14px auto 0}
.btn-blue{left:538px;top:1665px;width:122px;height:37px;border-radius:18px;background:var(--blue);color:#fff;font-size:10px;display:flex;align-items:center;justify-content:center;font-weight:500}

/* steps */
.steps{left:160px;top:1738px;width:881px;height:400px;background:#fff;border-radius:18px 18px 0 0}
.steps h2{font-family:'Russo One',sans-serif;color:var(--blue);font-size:31px;line-height:40px;letter-spacing:2px;text-align:center;margin-top:26px}
.steps h2 em{font-style:normal;color:var(--red2)}
.rule{width:110px;height:2px;background:var(--cyan);margin:14px auto 0;position:relative}
.rule:before,.rule:after{content:"";position:absolute;top:-3px;width:8px;height:8px;border-radius:50%;border:1.5px solid var(--cyan);background:#fff}
.rule:before{left:-4px}.rule:after{right:-4px}
.step{top:160px;width:260px;text-align:center}
.step .num{font-family:'Russo One',sans-serif;font-size:52px;line-height:60px;display:flex;align-items:center;justify-content:center;gap:6px}
.step h5{font-family:'Russo One',sans-serif;font-size:17.5px;line-height:24px;letter-spacing:1px;margin-top:22px}
.step p{font-size:10px;line-height:13px;color:#8893a3;margin-top:8px}
.step a{display:inline-block;margin-top:14px;font-size:10px;font-weight:700;color:var(--blue);border-bottom:1.5px solid var(--blue)}

/* review */
.review{left:0;top:2140px;width:1200px;height:266px;background:linear-gradient(135deg,#ececef,#f5f5f7 50%,#e6e6ea)}
.stars{color:var(--navy);font-size:18px;letter-spacing:3px}
.quote{left:159px;top:2195px;width:510px}
.quote p{color:var(--navy);font-size:16px;line-height:20px;margin-top:8px;font-weight:500}
.quote small{display:block;color:var(--sky);font-size:9px;margin-top:14px}
.badge{left:797px;top:2170px;width:210px;height:210px;border-radius:50%;background:#fff;border:2px solid var(--red2);text-align:center}
.arrow{width:14px;height:14px;border-left:2px solid var(--blue2);border-bottom:2px solid var(--blue2)}

/* founder */
.founder-text{left:577px;top:2448px;width:420px;color:var(--blue)}
.founder-text h3{font-family:'Russo One',sans-serif;font-size:13.5px;line-height:20px;letter-spacing:.5px}
.founder-text p{font-size:10.5px;line-height:12px;margin-top:12px;font-weight:500}
.btn-red{background:var(--red2);color:#fff;font-size:10px;font-weight:600;border-radius:4px;display:flex;align-items:center;justify-content:center}
.btn-ghost{border:1.5px solid var(--red2);color:var(--red2);font-size:10px;font-weight:600;border-radius:4px;display:flex;align-items:center;justify-content:center}

/* partners */
.partners{left:0;top:2822px;width:1200px;height:210px;background:var(--grey)}
.partners h2{font-family:'Russo One',sans-serif;color:var(--blue);font-size:27px;letter-spacing:2px;text-align:center;margin-top:24px}
.plogo{top:2925px;height:48px;background:#c9ccd3;border-radius:6px}

/* quote form */
.form{left:564px;top:3058px;width:478px}
.form h2{font-family:'Russo One',sans-serif;font-size:27px;letter-spacing:2px;color:#111}
.form label{display:block;font-size:11px;font-weight:600;margin-bottom:8px}
.field{background:#f1f2f4;height:34px}
.submit{width:88px;height:32px;background:var(--red2);color:#fff;font-size:13px;font-weight:600;border-radius:3px;display:flex;align-items:center;justify-content:center}

/* footer */
.footer{left:0;top:3520px;width:1200px;height:453px;background:linear-gradient(180deg,#4a3a72,#2f4a9a 55%,#1b55b0)}
.news{left:0;top:3543px;width:1200px;text-align:center;color:#fff}
.news h2{font-family:'Russo One',sans-serif;font-size:25px;letter-spacing:2px}
.news p{font-size:11px;margin-top:10px}
.fcol{top:3712px;color:#fff}
.fcol h6{font-family:'Russo One',sans-serif;font-size:14px;letter-spacing:1px;color:#9fd8f4;margin-bottom:10px}
.fcol p{font-size:10px;line-height:18px;color:#dfe7f5}
.fcol u{font-weight:600}
.legal{left:0;top:3946px;width:1200px;height:27px;color:#fff;font-size:11.5px;font-weight:700}
</style>
</head>
<body>

<!-- top utility bar -->
<div class="abs topbar">
  <div class="abs slant"></div>
  <nav class="abs"><span>ABOUT</span><span>CONSULTING</span><span>CONTACT</span></nav>
  <div class="abs social" style="left:1025px;top:10px"><i aria-label="Social profile"></i><i aria-label="Social profile"></i></div>
</div>

<!-- header -->
<header class="abs header">
  <div class="abs brand" style="left:24px;top:35px"><b></b><span>Maple Wren<br>Systems</span></div>
  <nav class="abs mainnav">
    <span>ELECTRONIC SECUITY ⌄</span><span>AUDIO + VIDEO ⌄</span><span>NETWORKING + COMMUNICATION ⌄</span><span>CABLING ⌄</span>
  </nav>
  <svg class="abs" style="left:944px;top:41px" width="22" height="22" viewBox="0 0 22 22" fill="none" stroke="#0054AA" stroke-width="2"><circle cx="9" cy="9" r="7"/><path d="M14 14l6 6"/></svg>
  <div class="abs quote-pill">REQUEST A QUOTE</div>
</header>

<!-- hero -->
<svg class="abs hero" viewBox="0 0 1200 500" preserveAspectRatio="none">
  <defs>
    <linearGradient id="heroGrad" x1="0" y1="0" x2="1" y2="0.6">
      <stop offset="0" stop-color="#e3202a"/>
      <stop offset="0.38" stop-color="#8a2a78"/>
      <stop offset="0.6" stop-color="#1f58b8"/>
      <stop offset="1" stop-color="#0a72d4"/>
    </linearGradient>
    <linearGradient id="waveGrad" x1="0" y1="0" x2="1" y2="0">
      <stop offset="0" stop-color="#1c5fc0"/><stop offset="1" stop-color="#0b86e0"/>
    </linearGradient>
  </defs>
  <path d="M0 0H1200V470C1050 500 920 460 800 470C620 485 520 510 360 470C220 440 110 390 0 410Z" fill="url(#waveGrad)"/>
  <path d="M0 0H1200V400C1080 410 980 430 860 440C700 455 560 470 420 440C260 410 130 390 0 405Z" fill="url(#heroGrad)"/>
</svg>
<div class="abs hero-copy">
  <div class="kicker">PROUDLY SERVING MIDDLE TENNESSEE</div>
  <div class="big" style="color:var(--red2);margin-top:6px">SAFER.</div>
  <div class="big">SMARTER.</div>
  <div class="big" style="color:#1a8ff0">FASTER.</div>
  <div class="sub">HOMES + BUSINESSES</div>
</div>

<!-- service cards -->
<div class="abs svc svc-red">
  <h3>AFFORDABLE SECURITY</h3>
  <ul><li>For Homes</li><li>For Businesses</li></ul>
  <div class="ph" role="img" aria-label="Photo of a woman arming a wall-mounted security keypad at home" style="background:linear-gradient(135deg,#d9d6d2,#8e8782)"></div>
  <div class="go" style="background:var(--blue)"></div>
</div>
<div class="abs svc svc-ice" style="left:463px;width:278px">
  <h3>ENVIABLE ENTERTAINMENT</h3>
  <ul><li>Home Theatres</li><li>Smart Homes</li><li>Whole Home A/V</li></ul>
  <div class="ph" role="img" aria-label="Photo of a dark home theatre room with a large screen" style="background:linear-gradient(135deg,#5d5a55,#2b2a2a)"></div>
  <div class="go" style="background:var(--red2)"></div>
</div>
<div class="abs svc svc-ice" style="left:759px;width:284px">
  <h3>CONNECTED BUSINESES</h3>
  <ul><li>Conference Systems</li><li>Phones</li><li>Networking</li><li>WiFi</li></ul>
  <div class="ph" role="img" aria-label="Photo of a business team on a video conference call" style="background:linear-gradient(135deg,#3c5a80,#1d2a3a)"></div>
  <div class="go" style="background:var(--red2)"></div>
</div>

<!-- connect + protect -->
<div class="abs h2red" style="top:1163px">CONNECT + PROTECT YOUR WORLD</div>
<div class="abs" style="left:0;top:1213px;width:1200px;text-align:center;color:var(--red2);font-size:16px">Lorem ipsum dolor sit amet, consectetuer adipiscing elit, sed diam</div>

<div class="abs band"></div>

<div class="abs feat" style="left:156px">
  <svg viewBox="0 0 42 42" fill="none" stroke="#0094D4" stroke-width="2"><path d="M12 28l8-8 8 8"/><path d="M10 14a14 14 0 0 1 22 0M14 18a9 9 0 0 1 14 0"/></svg>
  <h4>ENTRY &amp;<br>MOTION<br>SENSORS</h4>
  <p>Lorem ipsum dolor sit amet, consectetuer adipiscing elit, sed diam nonummy nibh euismod tincidunt ut laoreet dolore</p>
</div>
<div class="abs feat" style="left:338px">
  <svg viewBox="0 0 42 42" fill="none" stroke="#0094D4" stroke-width="2"><rect x="13" y="6" width="16" height="30" rx="4"/><circle cx="21" cy="14" r="3"/><path d="M17 28l4-6 4 6z"/></svg>
  <h4><br>VIDEO<br>MONITORING</h4>
  <p>Lorem ipsum dolor sit amet, consectetuer adipiscing elit, sed diam nonummy nibh euismod tincidunt ut laoreet dolore</p>
</div>
<div class="abs feat" style="left:521px">
  <svg viewBox="0 0 42 42" fill="none" stroke="#0094D4" stroke-width="2"><path d="M8 12l24 6-3 7-22-6z"/><path d="M16 22v8H8M8 26v8"/></svg>
  <h4><br>SECURITY<br>CAMERAS</h4>
  <p>Lorem ipsum dolor sit amet, consectetuer adipiscing elit, sed diam nonummy nibh euismod tincidunt ut laoreet dolore</p>
</div>
<div class="abs feat" style="left:703px">
  <div style="height:48px"></div>
  <h4>PET-<br>FRIENDLY</h4>
  <p>Lorem ipsum dolor sit amet, consectetuer adipiscing elit, sed diam nonummy nibh euismod tincidunt ut laoreet dolore</p>
</div>
<div class="abs feat" style="left:885px">
  <div style="height:36px"></div>
  <h4>FIRE &amp;<br>CARBON<br>MONOXIDE</h4>
  <p>Lorem ipsum dolor sit amet, consectetuer adipiscing elit, sed diam nonummy nibh euismod tincidunt ut laoreet dolore</p>
</div>

<div class="abs monitor">
  <h2>24/7<br>MONITORING</h2>
  <p>LOREM IPSUM DOLOR SIT AMET, CONSECTETUER ADIPISCING ELIT, SED DIAM NONUMMY NIBH EUISMOD TINCIDUNT UT LAOREET DOLORE MAGNA ALIQUAM ERAT VOLUTPAT. UT WISI ENIM</p>
</div>
<div class="abs btn-blue">BUTTON &nbsp;›</div>

<!-- steps -->
<section class="abs steps">
  <h2>A SAFER HOME OR BUSINESS IS<br>AS EASY AS <em>1-2-3</em></h2>
  <div class="rule"></div>
  <div class="abs step" style="left:0">
    <div class="num" style="color:var(--blue)">01<svg width="70" height="56" viewBox="0 0 70 56"><path d="M4 4h18l24 24-24 24H4l24-24z" fill="#0094D4"/><path d="M26 4h16l24 24-24 24H26l24-24z" fill="#6FCCEA"/></svg></div>
    <h5>BUILD AN<br><span style="color:var(--sky)">INSTANT QUOTE</span></h5>
    <p>Lorem ipsum dolor sit amet,<br>consectetuer adipiscing elit</p>
    <a>Get Started</a>
  </div>
  <div class="abs step" style="left:310px">
    <div class="num" style="color:var(--red2)">02<svg width="70" height="56" viewBox="0 0 70 56"><path d="M4 4h18l24 24-24 24H4l24-24z" fill="#e3202a"/><path d="M26 4h16l24 24-24 24H26l24-24z" fill="#EC4F4E"/></svg></div>
    <h5><span style="color:var(--red2)">SCHUDULE</span><br>INSTALLATION</h5>
    <p>Lorem ipsum dolor sit amet,<br>consectetuer adipiscing elit</p>
  </div>
  <div class="abs step" style="left:596px">
    <div class="num" style="color:var(--sky)">03<svg width="70" height="56" viewBox="0 0 70 56"><path d="M4 4h18l24 24-24 24H4l24-24z" fill="#00A9DD"/><path d="M26 4h16l24 24-24 24H26l24-24z" fill="#C7EBF8"/></svg></div>
    <h5>STAY SECURE<br><span style="color:#6FCCEA">24/7</span></h5>
    <p>Lorem ipsum dolor sit amet,<br>consectetuer adipiscing elit</p>
  </div>
</section>

<!-- review -->
<div class="abs review"></div>
<div class="abs arrow" style="left:134px;top:2267px;transform:rotate(45deg)"></div>
<div class="abs arrow" style="left:1030px;top:2267px;transform:rotate(-135deg)"></div>
<div class="abs quote">
  <div class="stars">★★★★★</div>
  <p>Fantastic sevice!! Used Brightline Alarm and HomeSentry in the past, and their custome sevice does not compare to Maple Wren! Installation and set up went smoothly!!! It's so convenient to use the apps remotely for the cameras, and arming or unarming the alarm. I'd rate them more than 5 stars it I was able to!</p>
  <small>~ Dana K. Cedar Hollow, TN</small>
</div>
<div class="abs badge">
  <div style="width:70px;height:70px;border-radius:50%;background:var(--blue2);margin:34px auto 0"></div>
  <div style="color:#f6b400;font-size:20px;letter-spacing:4px;margin-top:8px">★★★★★</div>
  <div style="color:var(--sky);font-size:17px;font-weight:500;letter-spacing:1px">REVIEWS</div>
</div>

<!-- founder -->
<svg class="abs" style="left:220px;top:2448px" width="290" height="290" viewBox="0 0 290 290">
  <circle cx="142" cy="142" r="138" fill="none" stroke="#e3202a" stroke-width="2"/>
</svg>
<div class="abs" role="img" aria-label="Portrait photo of the company founder" style="left:234px;top:2462px;width:258px;height:258px;border-radius:50%;background:linear-gradient(160deg,#b8bcc4,#4d5564)"></div>
<div class="abs" style="left:390px;top:2648px;width:136px;height:136px;border-radius:50%;background:#fff;border:3px solid var(--red2);display:flex;align-items:center;justify-content:center;text-align:center">
  <span style="font-family:'Russo One',sans-serif;color:var(--blue);font-size:14px;line-height:17px">Maple Wren<br>Systems</span>
</div>
<div class="abs founder-text">
  <h3>I FOUNDED MAPLE WREN SYSTEMS TO BRING TOGETHER TECHNOLOGY AND HONEST, RELIABLE SERVICE.</h3>
  <p style="margin-top:18px">I'm proud to call Tennessee home and even prouder to help keep its home and businesses secure.</p>
  <p>Whether it s protecting or elevating your space, my goal is to make technology work for you.</p>
  <p>Think of us as your friendly neighborhood tech expert here to safeguard what matters most.</p>
</div>
<div class="abs" role="img" aria-label="Handwritten founder signature, Elliot Marsh" style="left:580px;top:2652px;width:140px;height:54px;background:linear-gradient(90deg,#dbe7f5,#eef4fb);border-radius:4px"></div>
<div class="abs" style="left:577px;top:2736px;width:418px;height:1px;background:#999"></div>
<div class="abs btn-red" style="left:577px;top:2756px;width:168px;height:34px">TELL US HOW WE CAN HELP</div>
<div class="abs btn-ghost" style="left:758px;top:2756px;width:88px;height:34px">ABOUT US</div>

<!-- partners -->
<section class="abs partners">
  <h2>SERVICE PARTNERS</h2>
  <div class="rule" style="background:var(--red2)"></div>
</section>
<div class="abs arrow" style="left:132px;top:2944px;transform:rotate(45deg);border-color:#9fc3e6"></div>
<div class="abs arrow" style="left:1058px;top:2944px;transform:rotate(-135deg);border-color:#9fc3e6"></div>
<div class="abs plogo" style="left:156px;width:110px" aria-label="Partner badge"></div>
<div class="abs plogo" style="left:315px;width:160px" aria-label="Partner badge"></div>
<div class="abs plogo" style="left:515px;width:170px" aria-label="Partner badge"></div>
<div class="abs plogo" style="left:712px;width:200px" aria-label="Partner badge"></div>
<div class="abs plogo" style="left:932px;width:115px" aria-label="Partner badge"></div>

<!-- request a quote -->
<svg class="abs" style="left:0;top:3030px" width="520" height="490" viewBox="0 0 520 490">
  <path d="M0 70L494 0V490H0Z" fill="#0a86d8"/>
  <path d="M0 320L120 300V430L0 450Z" fill="#1c5fc0"/>
</svg>
<div class="abs" role="img" aria-label="Photo of a woman on a video call at her laptop" style="left:30px;top:3090px;width:448px;height:398px;background:linear-gradient(135deg,#cfd3d6,#6f7a6c 60%,#2f5a3a);clip-path:polygon(0 10%,100% 0,100% 100%,0 100%)"></div>
<div class="abs form">
  <h2>REQUEST A QUOTE</h2>
  <div style="display:flex;gap:18px;margin-top:26px">
    <div style="flex:1"><label>Name</label><div class="field"></div></div>
    <div style="flex:1"><label>Email*</label><div class="field"></div></div>
  </div>
  <div style="margin-top:22px"><label>Phone</label><div class="field"></div></div>
  <div style="margin-top:22px"><label>Message</label><div class="field" style="height:122px"></div></div>
  <div class="submit" style="margin-top:18px">Submit</div>
</div>

<!-- newsletter + footer -->
<footer class="abs footer"></footer>
<div class="abs news">
  <h2>SUBSCRIBE TO OUR NEWSLETTER</h2>
  <p>Security Tips, Special Offers and More!</p>
</div>
<div class="abs" style="left:348px;top:3614px;width:414px;height:34px;background:#fff;border-radius:3px;font-size:10px;color:#999;padding:10px 12px">Your email</div>
<div class="abs btn-red" style="left:773px;top:3614px;width:65px;height:34px;font-size:9px">SIGN UP</div>

<div class="abs fcol" style="left:132px">
  <div class="brand"><b style="background:#fff"></b><span style="color:#fff;font-size:17px">Maple Wren<br>Systems</span></div>
  <p style="margin-top:44px;font-size:9px;line-height:15px">PROUDLY SERVING<br>MIDDLE TENNESSEE</p>
  <div class="social" style="margin-top:14px;gap:18px"><i aria-label="Social profile"></i><i aria-label="Social profile"></i></div>
</div>
<div class="abs fcol" style="left:378px">
  <h6>CONTACT</h6>
  <p>420 Larkspur Way, Suite 2-118<br>Fernridge, TN 37000</p>
  <p><u>615.555.0142</u></p>
  <p><u>Request a Quote</u></p>
</div>
<div class="abs fcol" style="left:650px">
  <h6>RESIDENTIAL</h6>
  <p>Home Security<br>Smart Homes<br>Home Theatre +A/V<br>WiFi<br>Cabling</p>
</div>
<div class="abs fcol" style="left:922px">
  <h6>COMMERCIAL</h6>
  <p>Audio Video<br>Cabling<br>Communication<br>Electronic Security<br>Project Consulting</p>
</div>
<div class="abs" style="left:580px;top:3918px;width:40px;height:40px;border-radius:50%;background:#1b55b0;border:2px solid #9fd8f4;color:#fff;text-align:center;line-height:34px;font-size:18px">↑</div>
<div class="abs" style="left:1150px;top:3926px;width:26px;height:26px;border-radius:50%;background:#fff;color:var(--blue);text-align:center;line-height:24px;font-size:12px">⌃</div>
<div class="abs legal">
  <span class="abs" style="left:133px;top:6px">©2024 Maple Wren Systems. All rights reserved.</span>
  <span class="abs" style="left:862px;top:6px">Site Terms &nbsp;|&nbsp; Privacy Policy</span>
</div>

</body>
</html>
```